CONTEMPORARY Canva Art Design for Christians

I need a canvas art design on Christianity. The design must be in 3 SIMPLE dimensions: 12x 18 inches / 28 x 24 inches / 30 x 40 inches
The design must be accompanied by christian quote.
The christian quote can be "As For Me And My House We Will Serve The Lord (Joshua 24:15)" or any other quote that is good for display in a christian home.

I DON'T WANT THE TRADITIONAL CHRISTIAN DESIGN.. I WANT COLOURFUL, MEANINGFUL and CONTEMPORARY, MODERN DESIGN. And stay away from the scary image of Jesus in dark background, it only makes the home more scary not holy!

Target Market(s)

Christians

Colors

Designer to choose colors to be used in the design.

Requirements
Must have
• A graphic design and a christian quote that is powerful and edifies the soul. Great for display at home. Great use of colours to enhance the message.
Nice to have
• I wish to see great unique design with strong use of colours, images to enhance the scripture. It must glorify Jesus.
Should not have
• Should not be dull.

```html
<!DOCTYPE html>
<html lang="en">
<head>
<meta charset="UTF-8">
<title>As For Me And My House – Scripture Canvas</title>
<link rel="stylesheet" href="https://fonts.googleapis.com/css2?family=Tinos&family=Yellowtail&family=Roboto+Condensed:wght@300&display=swap">
<style>
  :root {
    --page-bg: #e9e9ea;
    --sky-deep: #0a2fae;
    --sky-mid: #2f6fd6;
    --sky-light: #8fc0f0;
    --glow: #ffffff;
    --ink: #0b0b0d;
    --ref-ink: #10214f;
  }
  html, body {
    margin: 0;
    width: 1200px;
    height: 1200px;
    overflow: hidden;
    background: var(--page-bg);
  }
  .canvas-art {
    position: absolute;
    left: 30px;
    top: 220px;
    width: 1140px;
    height: 760px;
    overflow: hidden;
  }
  .sky-scene {
    position: absolute;
    inset: 0;
    background:
      radial-gradient(ellipse 42% 48% at 50% 26%, var(--glow) 0%, rgba(255,255,255,0.85) 35%, rgba(255,255,255,0) 100%),
      radial-gradient(ellipse 70% 35% at 70% 72%, rgba(220,235,250,0.55) 0%, rgba(220,235,250,0) 100%),
      linear-gradient(180deg, var(--sky-light) 0%, var(--sky-mid) 55%, var(--sky-deep) 100%);
  }
  .scripture {
    position: absolute;
    inset: 0;
  }
  .caps { font-family: "Tinos", "Times New Roman", serif; fill: var(--ink); }
  .script { font-family: "Yellowtail", cursive; fill: var(--ink); }
  .reference { font-family: "Roboto Condensed", sans-serif; font-weight: 300; fill: var(--ref-ink); }
</style>
</head>
<body>
  <main class="canvas-art">
    <div class="sky-scene" role="img" aria-label="Bright blue sky with clouds and rays of light, a white dove with open wings descending in front of a glowing cross"></div>
    <svg class="scripture" viewBox="0 0 1140 760" width="1140" height="760">
      <g class="glow-cross" fill="#ffffff" opacity="0.55">
        <rect x="558" y="58" width="45" height="206"/>
        <rect x="446" y="152" width="267" height="43"/>
      </g>
      <text class="caps" x="154" y="423" font-size="60">AS FOR ME AND</text>
      <text class="script" x="365" y="494" font-size="78">My House</text>
      <text class="caps" x="932" y="494" font-size="52" text-anchor="end">WE WILL</text>
      <text class="caps" x="381" y="574" font-size="48">SERVE THE</text>
      <text class="script" x="645" y="640" font-size="175">Lord</text>
      <text class="reference" x="898" y="685" font-size="27">(JOSHUA 24:15)</text>
    </svg>
  </main>
</body>
</html>
```